Stationery Design Project

We need a stationery design for our Norwegian trucking company. We have existed for about 15 years and our 12 drivers uses relatively new vehicles to transport goods around in northern Norway. Long distance routes with fresh fish og food transport is our main operations.

We have already made alogo that's printed on our trucks. The logo and a picture of our trucks is attached. I think the logo i crappy, but since its already in use, changing it is not an option in this round. Still using a better colour scheme in the overall stationery and more interesting fonts is possible (altso in the logo).

Company details:
Name: Kjelvraket AS
Organisation nr 873 615 309
Post adress: 8642 Raudvik

I like minimalism and simplicity. I am avalibly for questions in normal GMT working hours either here or on mail: ivar@fjordlast.no

Reason: Hi. Im extending the deadline because I needed some time to find a vector file of our logo. Sorry for the inconvenience

Hi, and thanks for all your interest in the project. Some updates:

-          I have decided to commit to using one of the designs. Some designer will get the payment.

-          I have extended the deadline with 24 hours since I needed some time to find our firms vector logo (a slow Swedish man was holding me up)

-          We will not choose a design before the deadline. No need to rush.

-          We have received a lot of great design and think there is a need to specified the product we want to make:

o   Business Card for all our employers. I just need the design and will duplicate with the correct numbers and name myself. The information on should be: Logo, employer’s name, Phone number, email, website, Postal number and address. Use this as a template: logo, Leif Brattvoll, 47382066, Leif@fjordlast.no,, fjordlast.no, 8642 Raudvik. The order and placement of the information is your creative decision.

o   Stickers to put on the goods we travel. On the sticker the should be the following information: Logo, phone number, Tekst and link: Fraktæ av Kjelvraket. Ke du syns? Fjordlast.no/tilbakemelding (this means: Handled by Kjelvraket. What do you think Fjordlast.no/feedback -à the link will be a feedback form). The placement the information and size is your creative decision with some stings: we have been thinking of using Drukko for printing and see that a size about 6x6 cm, 8x5 or something like that. (with 3000 copies our budget is 200 punds). Any suggestions of other suppliers are welcome. Drukko price calculator http://www.drukkolabelhouse.co.uk/digital-litho-printing/printing-labels-tags/stickers/

o   Letterhead with logo, address, phone number and organizational number.

o   Envelopes with logo,address, phone number and organizational number.

Have a nice day.

 

 

• Using the blue colour in the logo and using a similar graphic approch.

```html
<!DOCTYPE html>
<html lang="no">
<head>
<meta charset="utf-8">
<title>Kjelvraket AS – visittkort</title>
<link rel="stylesheet" href="https://fonts.googleapis.com/css2?family=Open+Sans:wght@400;600;700&display=swap">
<style>
  :root {
    --blue: #0072bc;
    --blue-dark: #0b4ea2;
    --white: #ffffff;
    --backdrop: #b9bdc1;
    --ink: #2b2b2b;
  }
  html, body {
    margin: 0;
    padding: 0;
    width: 1200px;
    height: 732px;
    overflow: hidden;
    background: var(--backdrop);
    font-family: "Open Sans", Arial, sans-serif;
  }
  .sheet { position: relative; width: 1200px; height: 732px; }
  .card {
    position: absolute;
    width: 519px;
    height: 296px;
    overflow: hidden;
    box-shadow: 0 0 0 1px rgba(0,0,0,0.15);
  }
  .card--front { left: 64px; top: 44px; background: var(--white); }
  .card--back-white { left: 617px; top: 44px; background: var(--white); }
  .card--back-blue { left: 64px; top: 385px; background: var(--blue); }
  .card--back-dark { left: 617px; top: 383px; background: var(--blue-dark); }

  .card__swoosh { position: absolute; inset: 0; }

  .wordmark {
    position: absolute;
    left: 0; right: 0;
    text-align: center;
    font-weight: 700;
    font-size: 44px;
    letter-spacing: -0.5px;
    line-height: 1;
  }
  .wordmark--front { left: 20px; right: auto; width: 370px; top: 88px; color: var(--blue); }
  .card--back-white .wordmark { top: 128px; color: var(--blue); }
  .card--back-blue .wordmark,
  .card--back-dark .wordmark { top: 128px; color: var(--white); }

  .web-line {
    position: absolute;
    left: 0; right: 0;
    top: 248px;
    text-align: center;
    font-size: 16px;
    letter-spacing: 3.5px;
  }
  .card--back-white .web-line { color: var(--ink); }
  .card--back-blue .web-line,
  .card--back-dark .web-line { color: var(--white); }

  .holder {
    position: absolute;
    left: 27px; top: 217px;
    margin: 0;
    font-size: 18px;
    font-weight: 700;
    color: var(--blue);
  }
  .postal {
    position: absolute;
    left: 27px; top: 251px;
    font-size: 13px;
    color: var(--ink);
    display: flex; align-items: center; gap: 4px;
  }
  .contact {
    position: absolute;
    right: 20px; top: 202px;
    margin: 0; padding: 0;
    list-style: none;
    text-align: right;
    color: var(--white);
    font-size: 13.5px;
    line-height: 20px;
  }
  .contact li { display: flex; justify-content: flex-end; align-items: center; gap: 5px; }
  .contact svg, .postal svg { width: 10px; height: 10px; }
</style>
</head>
<body>
<main class="sheet">

  <section class="card card--front" aria-label="Visittkort, forside">
    <svg class="card__swoosh" viewBox="0 0 519 296" aria-hidden="true">
      <path d="M448 0 C425 160 310 245 155 296 L519 296 L519 0 Z" fill="var(--blue)"/>
      <path d="M476 0 C452 170 335 258 192 296 L519 296 L519 0 Z" fill="var(--blue-dark)"/>
    </svg>
    <div class="wordmark wordmark--front">Kjelvraket</div>
    <h1 class="holder">Leif Brattvoll</h1>
    <div class="postal">
      <svg viewBox="0 0 10 10" aria-hidden="true"><path d="M1 5 L5 1.5 L9 5 V9 H1 Z" fill="var(--blue)"/></svg>
      8642 Raudvik
    </div>
    <ul class="contact">
      <li><svg viewBox="0 0 10 10" aria-hidden="true"><path d="M2 1 L4 1 L5 3.5 L3.8 4.5 Q5 6.5 6 6.5 L7 5.3 L9 6.3 L9 8.3 Q4 9.5 1 2.5 Z" fill="var(--white)"/></svg>47382066</li>
      <li>Org nr 873 615 309</li>
      <li><svg viewBox="0 0 10 10" aria-hidden="true"><rect x="0.5" y="2" width="9" height="6.5" fill="var(--white)"/><path d="M0.5 2 L5 5.5 L9.5 2" stroke="var(--blue-dark)" fill="none"/></svg>Leif@fjordlast.no</li>
      <li><svg viewBox="0 0 10 10" aria-hidden="true"><circle cx="5" cy="5" r="4.2" fill="none" stroke="var(--white)"/><path d="M0.8 5 H9.2 M5 0.8 V9.2" stroke="var(--white)"/></svg>www.fjordlast.no</li>
    </ul>
  </section>

  <section class="card card--back-white" aria-label="Visittkort, bakside hvit">
    <div class="wordmark">Kjelvraket</div>
    <div class="web-line">www.fjordlast.no</div>
  </section>

  <section class="card card--back-blue" aria-label="Visittkort, bakside blå">
    <div class="wordmark">Kjelvraket</div>
    <div class="web-line">www.fjordlast.no</div>
  </section>

  <section class="card card--back-dark" aria-label="Visittkort, bakside mørkeblå">
    <div class="wordmark">Kjelvraket</div>
    <div class="web-line">www.fjordlast.no</div>
  </section>

</main>
</body>
</html>
```